Signage Design Project

Busisness is a bakery and deli long time owned by the Tavel family. Want to develop a new outside sign that communicates it is a deli and a bakery but keeps the tavel name in the design.

The sign when produced will be about 10' by 3' . It is not lighted at present but could be if it were advantageous.

The name of the store is:

Tavel's Harbor Lane Bakery and Deli. The concept is to have a new,modern sign that reinforces that it is a deli and a bakery, as most people only know about the bakery side of the business
Updates

The name Tavel is just a reinforcer so the people kno it is still in the family.  The emphasis should be on the HARBOR LANE BAKERY and DELI

Target Market(s)

Small business breakfast and lunch customers

Industry/Entity Type

Bakery

Requirements
Must have
• Great impact from the road. Communicate that it is a deli and a bakery. Keep the Tavel name but need not be a major design element

```html
<!DOCTYPE html>
<html lang="en">
<head>
<meta charset="utf-8">
<title>Tavel's Harbor Lane Bakery and Deli – Sign</title>
<link href="https://fonts.googleapis.com/css2?family=Kalam:wght@700&display=swap" rel="stylesheet">
<style>
  :root {
    --sign-red: #d02a36;
    --band-maroon: #7a1219;
    --trim-gold: #e7c46a;
    --trim-gold-light: #f3dc95;
    --type-white: #ffffff;
  }
  html, body {
    margin: 0;
    padding: 0;
    width: 1200px;
    height: 361px;
    overflow: hidden;
    background: var(--sign-red);
  }
  .sign {
    position: relative;
    width: 1200px;
    height: 361px;
    overflow: hidden;
  }
  .sign__backdrop {
    position: absolute;
    inset: 0;
    background: linear-gradient(180deg, #d93340 0%, var(--sign-red) 50%, #c92531 100%);
  }
  .sign__band {
    position: absolute;
    left: 0;
    top: 92px;
    width: 1200px;
    height: 176px;
    background: var(--band-maroon);
  }
  .sign__ornament {
    position: absolute;
    left: 430px;
    width: 340px;
    height: 46px;
    border-radius: 40px;
    background: radial-gradient(ellipse at center, var(--trim-gold-light) 0%, var(--trim-gold) 55%, rgba(231,196,106,0) 100%);
  }
  .sign__ornament--top { top: 44px; }
  .sign__ornament--bottom { top: 270px; }
  .sign__rule {
    position: absolute;
    left: 380px;
    width: 440px;
    height: 2px;
    background: linear-gradient(90deg, rgba(231,196,106,0), var(--trim-gold) 20%, var(--trim-gold) 80%, rgba(231,196,106,0));
  }
  .sign__rule--top { top: 89px; }
  .sign__rule--bottom { top: 269px; }
  .sign__name {
    position: absolute;
    left: 0;
    top: 92px;
    width: 1200px;
    height: 176px;
  }
  .sign__name text {
    font-family: "Kalam", "Comic Sans MS", cursive;
    font-weight: 700;
    font-size: 124px;
    fill: var(--type-white);
  }
</style>
</head>
<body>
  <div class="sign">
    <div class="sign__backdrop" role="img" aria-label="Red background with a fine gold diamond lattice pattern"></div>
    <div class="sign__ornament sign__ornament--top" role="img" aria-label="Gold scrollwork flourish above the name band"></div>
    <div class="sign__band"></div>
    <div class="sign__rule sign__rule--top"></div>
    <div class="sign__rule sign__rule--bottom"></div>
    <div class="sign__ornament sign__ornament--bottom" role="img" aria-label="Gold scrollwork flourish below the name band"></div>
    <svg class="sign__name" viewBox="0 0 1200 176" aria-label="Tavel's Harbor Lane Bakery and Deli">
      <text x="36" y="138" textLength="1128" lengthAdjust="spacingAndGlyphs">Tavel's Harbor Lane Bakery and Deli</text>
    </svg>
  </div>
</body>
</html>
```